Flyer Design in Photoshop PSD format needed

Christmas Production Flyer - DL (Horizontal) 210 wide x 100 deep

Final file to have elements as layered .psd

We need a flyer design to promote our upcoming Christmas Production which will be based on a movie premier.

Target Market(s)

Young Families Young Adult

Industry/Entity Type

Movie

Requirements
Must have
• The design should look like a Movie poster or Movie Premier advertisement.
Movie Title: Lantern (Main line, focal point) of Homecoming (Tag line, possibly italicised)
Dates: 16th and 18th of December
Time: 7pm
Tickets: Booking Online
Price: Free
Address: The Velmont 482 Parrow St Newcastle
Presented by - Fellowship42

In the strip at the bottom
Parking available at Dorvale and Kestrel Rest
Starring: Baby Jesus, Mary, Joseph, Gabriel, Choir of Angels

(Colours - midnight style theme/night sky/stars - not heaps of colour - dramatic)
Nice to have
• Theme:
Like as on movie posters e.g. starring. Avorel Film festival premier glitz and glam. Monaco.
Star sitting above middle (left to right) shining down onto a manger
Black strip at the bottom like in a movie poster containing most of the info regarding the event.
Should not have
• Snow
Christmas Tree, bobbles and presents, tinsel not kitch

```html
<!DOCTYPE html>
<html lang="en">
<head>
<meta charset="utf-8">
<title>Lantern of Homecoming – Christmas Production Flyer</title>
<link rel="stylesheet" href="https://fonts.googleapis.com/css2?family=League+Gothic&family=Tinos:ital,wght@0,400;1,400&family=Arimo:wght@700&display=swap">
<style>
  :root {
    --page: #ffffff;
    --sky-top: #0a1696;
    --sky-mid: #2a6fd2;
    --sky-glow: #5efcff;
    --strip: #000000;
    --ink-light: #ffffff;
    --star: #ffffff;
    --star-halo: #c9b8ff;
    --manger: #05060c;
  }
  html, body {
    margin: 0;
    width: 1200px;
    height: 901px;
    overflow: hidden;
    background: var(--page);
  }
  .flyer {
    position: absolute;
    left: 81px;
    top: 226px;
    width: 1037px;
    height: 494px;
    background: linear-gradient(to bottom, var(--sky-top) 0%, var(--sky-mid) 38%, var(--sky-glow) 72%, var(--sky-glow) 100%);
    overflow: hidden;
  }
  .starfield {
    position: absolute;
    inset: 0;
  }
  .title {
    position: absolute;
    left: 0;
    right: 0;
    top: 62px;
    text-align: center;
    color: var(--ink-light);
    font-family: "Tinos", "Times New Roman", serif;
  }
  .title-main {
    margin: 0;
    font-size: 98px;
    line-height: 1;
    font-weight: 400;
    letter-spacing: 1px;
    text-shadow: 0 2px 6px rgba(0, 0, 40, 0.35);
  }
  .title-tagline {
    margin: 6px 0 0;
    font-size: 40px;
    line-height: 1;
    letter-spacing: 12px;
    text-shadow: 0 2px 4px rgba(0, 0, 40, 0.3);
  }
  .title-tagline em {
    font-style: italic;
    letter-spacing: 10px;
    margin-right: 14px;
  }
  .manger-art {
    position: absolute;
    left: 381px;
    top: 244px;
    width: 276px;
    height: 138px;
    border-radius: 60px 60px 0 0;
    background: linear-gradient(to bottom, rgba(5, 6, 12, 0.75), var(--manger));
  }
  .info-strip {
    position: absolute;
    left: 0;
    right: 0;
    bottom: 0;
    height: 112px;
    background: var(--strip);
    color: var(--ink-light);
    font-family: "League Gothic", "Arial Narrow", sans-serif;
    display: flex;
    flex-direction: column;
    justify-content: center;
    gap: 4px;
  }
  .info-row {
    display: flex;
    justify-content: center;
    align-items: flex-start;
    gap: 12px;
    font-size: 27px;
    line-height: 1;
    letter-spacing: 0.3px;
  }
  .info-item {
    display: flex;
    align-items: flex-start;
    gap: 4px;
  }
  .cast {
    display: flex;
    gap: 12px;
  }
  .label {
    font-size: 11px;
    padding-top: 2px;
    letter-spacing: 0.2px;
  }
  .label-stack {
    display: flex;
    flex-direction: column;
    align-items: center;
  }
  .dates {
    font-family: "Arimo", Arial, sans-serif;
    font-weight: 700;
    font-size: 24px;
    padding-top: 2px;
    margin: 0 4px;
  }
</style>
</head>
<body>
  <main class="flyer">
    <svg class="starfield" width="1037" height="494" viewBox="0 0 1037 494" aria-hidden="true">
      <defs>
        <symbol id="sparkle" viewBox="-10 -10 20 20">
          <circle r="3" fill="var(--star-halo)" opacity="0.6"/>
          <path d="M0 -10 L1 -1 L10 0 L1 1 L0 10 L-1 1 L-10 0 L-1 -1 Z" fill="var(--star)"/>
        </symbol>
      </defs>
      <use href="#sparkle" x="121" y="30" width="12" height="12"/>
      <use href="#sparkle" x="180" y="57" width="24" height="24"/>
      <use href="#sparkle" x="53" y="78" width="14" height="14"/>
      <use href="#sparkle" x="268" y="104" width="18" height="18"/>
      <use href="#sparkle" x="96" y="126" width="22" height="22"/>
      <use href="#sparkle" x="162" y="170" width="26" height="26"/>
      <use href="#sparkle" x="32" y="210" width="12" height="12"/>
      <use href="#sparkle" x="116" y="224" width="10" height="10"/>
      <use href="#sparkle" x="853" y="28" width="18" height="18"/>
      <use href="#sparkle" x="711" y="61" width="12" height="12"/>
      <use href="#sparkle" x="969" y="57" width="26" height="26"/>
      <use href="#sparkle" x="888" y="90" width="20" height="20"/>
      <use href="#sparkle" x="791" y="114" width="12" height="12"/>
      <use href="#sparkle" x="944" y="148" width="10" height="10"/>
      <use href="#sparkle" x="870" y="194" width="20" height="20"/>
      <use href="#sparkle" x="973" y="204" width="18" height="18"/>
    </svg>

    <header class="title">
      <h1 class="title-main">LANTERN</h1>
      <p class="title-tagline"><em>of</em>HOMECOMING</p>
    </header>

    <div class="manger-art" role="img" aria-label="Silhouette of a wooden manger filled with straw, lit from behind by the night sky glow"></div>

    <section class="info-strip">
      <div class="info-row">
        <div class="info-item">
          <span class="label">STARRING</span>
          <span class="cast">
            <span>BABY JESUS</span><span>MARY</span><span>JOSEPH</span><span>GABRIEL</span><span>CHOIR OF ANGELS</span>
          </span>
        </div>
        <div class="info-item"><span class="label">TIME</span><span>7PM</span></div>
        <div class="info-item"><span class="label">TICKETS</span><span>BOOKING ONLINE</span></div>
        <div class="info-item"><span class="label">PRICE</span><span>FREE</span></div>
        <div class="info-item">
          <span class="label label-stack"><span>PRESENTED</span><span>BY</span></span>
          <span>FELLOWSHIP42</span>
        </div>
      </div>
      <div class="info-row">
        <div class="info-item"><span class="label">ADDRESS</span><span>THE VELMONT 482 PARROW ST NEWCASTLE</span></div>
        <span class="dates">DECEMBER 16 AND 18</span>
        <div class="info-item"><span class="label">PARKING</span><span>AVAILABLE AT DORVALE AND KESTREL REST</span></div>
      </div>
    </section>
  </main>
</body>
</html>
```